Chilli Sauce - Label for Chilli Sauce bottle

I want a design for my chilli sauce label. I have included an example from an existing product. The key features of a successful design are as follows:
1. It shows the supplier: Bramble Ridge Condiments or Bramble Ridge if a shorter label fits better.
2. We need to have space for the ingredients. We will add these after.
3. Simple is good, refer attached. It doesn't need to be a design/logo, but a great design would be wonderful.
4. Some ideas. Bramble Ridge at the top of the label. Chilli Sauce in the middle of the label. Made with local ingredients (optional). Contains chilli - believe it or not (optional or similar wording)

```html
<!DOCTYPE html>
<html lang="en">
<head>
<meta charset="utf-8">
<title>Bramble Ridge Condiments – Chilli Sauce Label</title>
<link href="https://fonts.googleapis.com/css2?family=Bebas+Neue&family=Kaushan+Script&family=Roboto+Condensed:wght@300;400;700&family=Arimo:wght@400;700&display=swap" rel="stylesheet">
<style>
  :root{
    --page:#ffffff;
    --label:#060606;
    --white:#ffffff;
    --gold:#fcc414;
    --brush:#b3201f;
    --flame-a:#f7a21b;
    --flame-b:#e8411f;
    --nutri-ink:#111111;
  }
  *{box-sizing:border-box;margin:0;padding:0}
  html,body{width:900px;height:1200px;overflow:hidden;background:var(--page)}
  .canvas{position:relative;width:900px;height:1200px}
  .label{position:absolute;left:20px;top:405px;width:860px;height:391px;background:var(--label);color:var(--white)}

  /* nutrition panel */
  .nutrition{position:absolute;left:42px;top:41px;width:158px;background:var(--white);color:var(--nutri-ink);
    border:1px solid var(--nutri-ink);padding:2px 3px;font-family:"Arimo",Arial,sans-serif;font-size:5.6px;line-height:1.35}
  .nutrition h2{font-size:15px;font-weight:700;letter-spacing:.6px;line-height:1;border-bottom:1px solid var(--nutri-ink);padding-bottom:1px}
  .nutrition .row{display:flex;justify-content:space-between;border-top:.5px solid #777}
  .nutrition .row.indent{padding-left:8px}
  .nutrition .row.indent2{padding-left:18px}
  .nutrition .servings{font-size:7px}
  .nutrition .serving-size{font-size:7.5px;font-weight:700;border-bottom:5px solid var(--nutri-ink);display:flex;justify-content:space-between}
  .nutrition .amount{font-weight:700;font-size:5.5px}
  .nutrition .calories{display:flex;justify-content:space-between;font-weight:700;font-size:13px;line-height:1;border-bottom:3px solid var(--nutri-ink);padding-bottom:1px}
  .nutrition .dv{text-align:right;font-weight:700;font-size:4.5px}
  .nutrition .end{border-bottom:3px solid var(--nutri-ink)}
  .nutrition .note{font-size:4.4px;line-height:1.3;padding-top:2px;border-bottom:.5px solid #777}
  .nutrition .note:last-child{border:none}

  .origin{position:absolute;left:42px;top:310px;width:158px;text-align:center;font-family:"Roboto Condensed",sans-serif;font-size:9.5px;line-height:1.25;font-weight:300;letter-spacing:.2px}
  .origin strong{font-weight:700}

  /* centre panel */
  .brand{position:absolute;left:280px;top:42px;width:300px;text-align:center}
  .brand-name{font-family:"Bebas Neue",sans-serif;font-size:44px;line-height:.9;letter-spacing:.5px;color:var(--white)}
  .brand-sub{font-family:"Kaushan Script",cursive;font-size:27px;line-height:1;color:var(--gold);margin-top:-4px}

  .product-art{position:absolute;left:320px;top:112px;width:230px;height:140px}
  .product-title{position:absolute;left:310px;top:112px;width:250px;font-family:"Kaushan Script",cursive;color:var(--gold);
    font-size:58px;line-height:.85;text-align:center}
  .product-title span{display:block}
  .product-title .second{padding-left:40px}

  .tagline{position:absolute;left:280px;top:268px;width:300px;text-align:center;font-family:"Kaushan Script",cursive;color:var(--gold);font-size:23px;line-height:1.15}
  .volume{position:absolute;left:280px;top:328px;width:300px;text-align:center;font-family:"Bebas Neue",sans-serif;font-size:27px;letter-spacing:.5px}

  /* right panel */
  .ingredients{position:absolute;left:640px;top:52px;width:170px;text-align:center;font-family:"Roboto Condensed",sans-serif;font-weight:300;font-size:8.6px;line-height:1.45;text-transform:uppercase}
  .heat{position:absolute;left:630px;top:180px;width:170px;height:150px}
  .heat-label{position:absolute;left:9px;top:40px;font-family:"Bebas Neue",sans-serif;font-size:15px}
  .heat-scale{position:absolute;left:28px;top:0;width:50px;height:140px}
  .heat-badge{position:absolute;left:80px;top:58px;width:78px;height:62px}
  .heat-text{position:absolute;left:80px;top:62px;width:78px;text-align:center;font-family:"Kaushan Script",cursive;color:var(--gold);font-size:21px;line-height:.9}
  .storage{position:absolute;left:620px;top:340px;width:220px;text-align:center;font-family:"Roboto Condensed",sans-serif;font-weight:700;font-size:9.5px;letter-spacing:.2px}
</style>
</head>
<body>
<div class="canvas">
  <section class="label">

    <aside class="nutrition">
      <h2>Nutrition Facts</h2>
      <div class="servings">24 servings per container</div>
      <div class="serving-size"><span>Serving size</span><span>1 tsp (5ml)</span></div>
      <div class="amount">Amount Per Serving</div>
      <div class="calories"><span>Calories</span><span>0</span></div>
      <div class="dv">% Daily Value*</div>
      <div class="row"><span><b>Total Fat</b> 0g</span><b>0%</b></div>
      <div class="row indent"><span>Saturated Fat 0g</span><b>0%</b></div>
      <div class="row indent"><span><i>Trans</i> Fat 0g</span><span></span></div>
      <div class="row"><span><b>Cholesterol</b> 0mg</span><b>0%</b></div>
      <div class="row"><span><b>Sodium</b> 90mg</span><b>4%</b></div>
      <div class="row"><span><b>Total Carbohydrate</b> 0g</span><b>0%</b></div>
      <div class="row indent"><span>Dietary Fiber 0g</span><b>0%</b></div>
      <div class="row indent"><span>Total Sugars 0g</span><span></span></div>
      <div class="row indent2"><span>Includes 0g Added Sugars</span><b>0%</b></div>
      <div class="row end"><span><b>Protein</b> 0g</span><b>0%</b></div>
      <p class="note">Not a significant source of vitamin D, calcium, iron, and potassium</p>
      <p class="note">*The % Daily Value (DV) tells you how much a nutrient in a serving of food contributes to a daily diet. 2,000 calories a day is used for general nutrition advice.</p>
    </aside>

    <p class="origin"><strong>PRODUCT OF AUSTRALIA</strong><br>DISTRIBUTED BY<br>BRAMBLE RIDGE CONDIMENTS</p>

    <header class="brand">
      <div class="brand-name">BRAMBLE RIDGE</div>
      <div class="brand-sub">Condiments</div>
    </header>

    <svg class="product-art" viewBox="0 0 230 140" role="img" aria-label="Red brush-stroke backdrop with an orange flame beside the product name">
      <rect x="0" y="28" width="215" height="100" fill="var(--brush)"/>
      <rect x="168" y="0" width="52" height="78" rx="26" fill="var(--flame-b)"/>
    </svg>
    <h1 class="product-title"><span>Chilli</span><span class="second">Sauce</span></h1>

    <p class="tagline">With Australian<br>Grown Chillies</p>
    <p class="volume">150 ML / 5.07 OZ</p>

    <p class="ingredients">Ingredients: water, chilli peppers, tomato, salt, spices, pH control agent (acetic acid), stabilizer (xanthan gum), acidifier (citric acid), sodium benzoate as a preservtive and FD&amp;C Red 40.</p>

    <div class="heat">
      <span class="heat-label">HOT</span>
      <svg class="heat-scale" viewBox="0 0 50 140" role="img" aria-label="Chilli pepper heat meter graded from green to red">
        <defs>
          <linearGradient id="heatGrad" x1="0" y1="0" x2="0" y2="1">
            <stop offset="0" stop-color="#e01f26"/>
            <stop offset=".45" stop-color="#f08a24"/>
            <stop offset=".75" stop-color="#f3e11b"/>
            <stop offset="1" stop-color="#3fb34f"/>
          </linearGradient>
        </defs>
        <rect x="12" y="10" width="26" height="128" rx="13" fill="url(#heatGrad)"/>
      </svg>
      <svg class="heat-badge" viewBox="0 0 78 62" role="img" aria-label="Red brush-stroke badge">
        <rect width="78" height="62" fill="var(--brush)"/>
      </svg>
      <div class="heat-text">Extra<br>Spice</div>
    </div>

    <p class="storage">KEEP IN A FRESH AND DRY PLACE</p>
  </section>
</div>
</body>
</html>
```